"Outside the Box" Newsletter Design Project-Communications Company

I am looking for an Internal newsletter for a communications company that will be sent to our sales and leadership team.
This newsletter will deliver forecasting, sales results, stack rankings for the sales reps, total team results, corporate updates, success stories and updates from Training/Operations/Sales/Marketing (could be a box for each)I would also need a couple sections with a blank header and box to add info as needed, if something comes up that is not set in stone weekly.
I am looking for a template that looks sharp and professional that i can use every week by just dropping content in, (text and possibly an employee picture) I will need it in a format (possibly word) that the will keep the text in line when I drop it in each week. Once complete I can save to a pdf and would like to have the ability to drop it into the body of an email.

We have a racecar theme that we use when training our sales folks so we would like a little bit of that to the newsletter and also incorporate our color scheme from our company.

I would like four versions of the newsletter..all would match other than the title.
1. Week 1 title - Start your engines
2. Week 2 title - Looking for suggestions
3. Week 3 title - Looking for suggestions
4. Week 4 title - Approaching the finish line, this version would also include an employee spotlight, one seperate section.

If we could include a few pics around racing that would be good, not over the top, just a few to give it a little of that feel. Maybe a checkered flag with the QV logo on it, a racecar..anything else that may make sense.

I will attach our logo and our organization is called SMB (small/medium business) so that should also be placed on there somewhere. Final design would need to be two pages, sharp professional feel, my Vice President likes a very clean look, not too busy. I have also attached a sample newsletter from another group in our company, ours will not have as much content, we are much smaller but this is a sample (on a smaller scale)of what we are looking for. The company look and feel is what we want to follow. Thank you

Target Market(s)

Our Internal sales team.

Industry/Entity Type

Communications

Requirements
Must have
• Ability to update with my content without having things shift and fall out of line..format that will make that easy and then able to save to PDF..2 pages long.
Nice to have
• HTML template to match.

```html
<!DOCTYPE html>
<html lang="en">
<head>
<meta charset="utf-8">
<title>QV Weekly Recap – Week 1</title>
<link rel="stylesheet" href="https://fonts.googleapis.com/css2?family=Open+Sans:wght@400;600;700&display=swap">
<style>
:root{
  --page:#efefef;
  --card:#ffffff;
  --purple:#7b2d8f;
  --ink:#222222;
  --text:#555555;
  --muted:#8a8a8a;
  --rule:#e2e2e2;
  --row-alt:#f6f6f6;
  --shadow:0 2px 6px rgba(0,0,0,.12);
}
*{box-sizing:border-box;margin:0;padding:0}
html,body{width:1200px;height:3846px;overflow:hidden}
body{background:var(--page);font-family:"Open Sans",Arial,sans-serif;color:var(--text);position:relative}
.card{position:absolute;background:var(--card);box-shadow:var(--shadow)}
p{font-size:17px;line-height:29px}
.btn{display:inline-block;border:2px solid #cfcfcf;border-radius:24px;padding:8px 30px;font-size:16px;color:var(--ink);background:#fafafa}

/* masthead */
.masthead{position:absolute;left:120px;top:50px;width:965px;height:130px}
.brand{position:absolute;left:0;top:30px}
.brand-name{font-size:30px;font-weight:600;color:var(--ink);line-height:1;letter-spacing:1px}
.issue{position:absolute;right:0;top:18px;text-align:right}
.issue-date{font-size:21px;font-weight:700;color:var(--ink);letter-spacing:.3px}
.issue-tag{font-size:17px;color:var(--text);margin-top:4px}

/* hero */
.hero{left:123px;top:192px;width:962px;height:780px}
.hero-head{height:104px;display:flex;align-items:center;padding-left:40px;gap:26px}
.flag-icon{width:52px;height:52px}
.hero-title{font-size:30px;font-weight:700;color:var(--ink)}
.hero-photo{height:396px;background:linear-gradient(135deg,#2a2a33 0%,#6f6f7c 45%,#c9c9d2 60%,#3a3a44 100%)}
.hero-body{padding:34px 40px 0}
.hero-body .btn{margin-top:26px}

/* news briefs */
.brief{left:123px;width:608px;height:282px;padding:30px 30px 0 0}
.brief-1{top:1008px}
.brief-2{top:1328px}
.date-badge{position:absolute;left:0;top:30px;width:115px;height:115px;background:var(--purple);color:#fff;text-align:center;padding-top:18px}
.date-badge .day{font-size:38px;font-weight:600;line-height:1}
.date-badge .mon{font-size:15px;font-weight:600;letter-spacing:1px;margin-top:6px}
.brief-content{margin-left:146px}
.brief-title{font-size:27px;font-weight:700;color:var(--ink);margin-bottom:12px}
.brief-content .btn{margin-top:22px}

/* events */
.events{left:761px;top:1008px;width:324px;height:607px;text-align:center;padding-top:28px}
.events-title{font-size:27px;font-weight:700;color:var(--ink);margin-bottom:26px}
.event{margin-bottom:34px}
.event-date{font-size:18px;color:var(--purple);line-height:28px}
.event-name{font-size:18px;color:var(--ink);line-height:28px}

/* ranking table */
.ranking{left:123px;top:1646px;width:962px;height:527px;overflow:hidden}
.ranking table{width:100%;border-collapse:collapse}
.ranking th{background:var(--purple);color:#fff;font-size:19px;font-weight:700;text-align:left;height:104px}
.ranking td{font-size:17px;color:var(--text);height:84.6px;border-top:1px solid var(--rule)}
.ranking tr:nth-child(even) td{background:var(--row-alt)}
.ranking .c-rank{padding-left:31px;width:154px}
.ranking .c-rep{width:434px}
.ranking .c-mtd{width:200px}

/* leaders */
.leader{top:2219px;width:266px;height:550px;padding:22px 22px 0}
.leader-1{left:123px}
.leader-2{left:461px}
.leader-3{left:805px}
.leader-photo{height:395px;background:linear-gradient(180deg,#e4e4e4 0%,#8a7a70 55%,#4a3d38 100%)}
.leader-role{font-size:16px;font-weight:700;color:var(--ink);margin-top:24px}
.leader-line{display:flex;justify-content:space-between;font-size:16px;color:var(--ink);margin-top:6px}

/* success story */
.story{left:123px;top:2808px;width:962px;height:846px}
.story-head{position:absolute;left:34px;top:22px;font-size:27px;line-height:36px;font-weight:700;color:var(--ink)}
.story-photo{position:absolute;left:0;top:82px;width:300px;height:290px;background:linear-gradient(160deg,#c9c2b8 0%,#8c7d6e 50%,#3f3832 100%)}
.story-lead{position:absolute;left:345px;top:92px;width:590px}
.story-title{font-size:22px;font-weight:700;color:var(--ink);margin-bottom:10px}
.story-record{position:absolute;left:34px;top:420px;width:580px}
.story-record .story-title{margin-bottom:14px}
.stat-table{position:absolute;left:635px;top:482px;width:310px;border-collapse:collapse;font-size:11px;color:var(--ink)}
.stat-table caption{background:#29a3dd;color:#fff;font-size:10px;font-weight:700;text-align:left;padding:3px 6px}
.stat-table th{background:#29a3dd;color:#fff;font-weight:700;padding:3px 6px;text-align:right}
.stat-table td{padding:2px 6px;text-align:right;border-bottom:1px solid #d7e9f4}
.stat-table td:first-child,.stat-table th:first-child{text-align:left}

/* footer */
.footer{position:absolute;left:150px;top:3684px;width:900px;text-align:center;font-size:14px;line-height:24px;color:var(--muted)}
.footer a{color:var(--purple);font-weight:600}
</style>
</head>
<body>

<header class="masthead">
  <div class="brand"><span class="brand-name">QV</span></div>
  <div class="issue">
    <div class="issue-date">DECEMBER 20, 2012 ISSUE</div>
    <div class="issue-tag">A Weekly Recap of Important Things Going on QV That You Need To Know</div>
  </div>
</header>

<section class="card hero">
  <div class="hero-head">
    <svg class="flag-icon" viewBox="0 0 52 52" aria-hidden="true">
      <rect x="6" y="6" width="40" height="40" fill="#2b2b2b"/>
      <rect x="6" y="6" width="10" height="10" fill="#fff"/><rect x="26" y="6" width="10" height="10" fill="#fff"/>
      <rect x="16" y="16" width="10" height="10" fill="#fff"/><rect x="36" y="16" width="10" height="10" fill="#fff"/>
      <rect x="6" y="26" width="10" height="10" fill="#fff"/><rect x="26" y="26" width="10" height="10" fill="#fff"/>
      <rect x="16" y="36" width="10" height="10" fill="#fff"/><rect x="36" y="36" width="10" height="10" fill="#fff"/>
    </svg>
    <h1 class="hero-title">WEEK 1 - Start your engines</h1>
  </div>
  <div class="hero-photo" role="img" aria-label="Close-up photo of a racing helmet with a checkered stripe"></div>
  <div class="hero-body">
    <p>Far far away, behind the word mountains, far from the countries Vokalia and Consonantia, there live the blind texts. Separated they live in Bookmarksgrove right at the coast of the Semantics, a large language ocean. A small river named Duden flows by their place and supplies it with the necessary regelialia. It is a paradisematic country, in which roasted parts of sentences fly into your mouth.</p>
    <span class="btn">Read More</span>
  </div>
</section>

<article class="card brief brief-1">
  <div class="date-badge"><div class="day">16</div><div class="mon">AUG</div></div>
  <div class="brief-content">
    <h2 class="brief-title">Long Big Headline Title Here</h2>
    <p>Far far away, behind the word mountains, far from the countries Vokalia and Consonantia, there live the blind texts. Separated they live in</p>
    <span class="btn">Read More</span>
  </div>
</article>

<article class="card brief brief-2">
  <div class="date-badge"><div class="day">16</div><div class="mon">AUG</div></div>
  <div class="brief-content">
    <h2 class="brief-title">Long Big Headline Title Here</h2>
    <p>Far far away, behind the word mountains, far from the countries Vokalia and Consonantia, there live the blind texts. Separated they live in</p>
    <span class="btn">Read More</span>
  </div>
</article>

<aside class="card events">
  <h2 class="events-title">Upcoming Event</h2>
  <div class="event"><div class="event-date">Mon, July 23</div><div class="event-name">CR Q2 Wrap-Up Presenta-<br>tion @ 3 pm</div></div>
  <div class="event"><div class="event-date">Fri, August 3</div><div class="event-name">Chicago Mid-Year Town<br>Hall</div></div>
  <div class="event"><div class="event-date">June 1—August 31</div><div class="event-name">Double Down Challenge</div></div>
  <div class="event"><div class="event-date">June 1—August 31</div><div class="event-name">CR TooHot To Handle<br>Contest</div></div>
</aside>

<section class="card ranking">
  <table>
    <thead>
      <tr><th class="c-rank">Rank</th><th class="c-rep">Sales Rep Name</th><th class="c-mtd">Total MTD</th><th>Total Ptc</th></tr>
    </thead>
    <tbody>
      <tr><td class="c-rank">1</td><td>Hallworth, Jon T</td><td>USD $ 50,000</td><td>90%</td></tr>
      <tr><td class="c-rank">2</td><td>Hallworth, Jon T</td><td>USD $ 40,000</td><td>80%</td></tr>
      <tr><td class="c-rank">3</td><td>Marchetti, Christopher A</td><td>USD $ 30,000</td><td>70%</td></tr>
      <tr><td class="c-rank">4</td><td>Marchetti, Christopher A</td><td>USD $ 20,000</td><td>60%</td></tr>
      <tr><td class="c-rank">5</td><td>Lindqvist, Brady J</td><td>USD $ 15,000</td><td>20%</td></tr>
    </tbody>
  </table>
</section>

<div class="card leader leader-1">
  <div class="leader-photo" role="img" aria-label="Portrait photo of the top sales rep wearing a chef hat"></div>
  <div class="leader-role">TOP REP</div>
  <div class="leader-line"><span>CORSO</span><span>70%</span></div>
</div>
<div class="card leader leader-2">
  <div class="leader-photo" role="img" aria-label="Portrait photo of the top LCM wearing a chef hat"></div>
  <div class="leader-role">TOP LCM</div>
  <div class="leader-line"><span>MARISA</span><span>80%</span></div>
</div>
<div class="card leader leader-3">
  <div class="leader-photo" role="img" aria-label="Portrait photo of the top manager wearing a chef hat"></div>
  <div class="leader-role">TOP MANAGER</div>
  <div class="leader-line"><span>HOLLAND</span><span>90%</span></div>
</div>

<section class="card story">
  <h2 class="story-head">Success Story</h2>
  <div class="story-photo" role="img" aria-label="Photo of the featured employee seated in a casual pose"></div>
  <div class="story-lead">
    <h3 class="story-title">Say Hello For Daniel Brookes From England.</h3>
    <p>Lorem ipsum dolor sit amet, consectetuer adipiscing elit. Aenean commodo ligula eget dolor. Aenean massa. Cum sociis natoque penatibus et magnis dis parturient montes, nascetur ridiculus mus. Donec quam felis, ultricies nec, pellentesque eu, pretium quis, sem. Nulla consequat massa quis enim. Donec pede justo, fringilla vel, aliquet nec, vulputate eget, arcu. In enim justo, rhoncus ut, imperdiet a, venenatis vitae, justo. Nullam dictum felis eu pede mollis pretium. Integer tincidunt. Cras dapibus.</p>
  </div>
  <div class="story-record">
    <h3 class="story-title">Daniel Brookes Record?</h3>
    <p>Lorem ipsum dolor sit amet, consectetuer adipiscing elit. Aenean commodo ligula eget dolor. Aenean massa. Cum sociis natoque penatibus et magnis dis parturient montes, nascetur ridiculus mus. Donec quam felis, ultricies nec, pellentesque eu, pretium quis, sem. Nulla consequat massa quis enim. Donec pede justo, fringilla vel, aliquet nec, vulputate eget, arcu. In enim justo, rhoncus ut, imperdiet a, venenatis vitae, justo. Nullam dictum felis eu pede mollis pretium. Integer tincidunt. Cras dapibus.</p>
  </div>
  <table class="stat-table">
    <caption>LCM RANKINGS</caption>
    <tr><th>LCM</th><th>July MTD</th><th>July Pct</th></tr>
    <tr><td>Farrow</td><td>22,761</td><td>23%</td></tr>
    <tr><td>Kendal</td><td>19,402</td><td>21%</td></tr>
    <tr><td>Thornton</td><td>15,031</td><td>18%</td></tr>
    <tr><td>Garner</td><td>$0</td><td>0%</td></tr>
    <tr><td>Flynn</td><td>$0</td><td>0%</td></tr>
    <tr><td>Walton</td><td>$0</td><td>0%</td></tr>
    <tr><td>Price</td><td>$0</td><td>0%</td></tr>
    <tr><td>Ashby</td><td>$0</td><td>0%</td></tr>
    <tr><td>Monroe</td><td>$0</td><td>0%</td></tr>
    <tr><td>Total</td><td>57,194</td><td>14%</td></tr>
  </table>
</section>

<footer class="footer">
  Sed ut perspiciatis unde omnis iste natus error sit voluptatem accusantium doloremque laudantium, totam rem aperiam, eaque ipsa quae ab illo inventore veritatis et quasi architecto beatae vitae dicta sunt explicabo. Nemo enim ipsam voluptatem quia voluptas sit aspernatur aut odit aut fugit, sed quia consequuntur magni dolores eos qui ratione voluptatem sequi nesciunt. <a>Unsubscribe Newsletter Here</a>
</footer>

</body>
</html>
```